www.marvenholt.com

Updating website so looks futristic but yet business like and easy to navigate, essentially a good landing page with a cool picture summing up what we do, and links to the following pages, all other pages on site to be updated, Exclusive Distributor of Brisk Forge Unique Fitness Equipment Products in UK & Ireland, www.crestvolley.co.uk Exclusive Partners & Distributors Of Crest Volley - Obstacle Races - Obstacle Hire - Obstacle Training - Adventure Events, www.goplumwick.co.uk Adventures That Inspire. We also Health Club / Facillity Consultancy

```html
<!DOCTYPE html>
<html lang="en">
<head>
<meta charset="utf-8">
<title>Marven Holt — Health, Wellness, Fitness, Consultants</title>
<link rel="stylesheet" href="https://fonts.googleapis.com/css2?family=Cinzel:wght@400;700&family=Raleway:wght@400;600;700&family=Open+Sans:wght@400;600&family=Cormorant+Garamond:wght@500&display=swap">
<style>
:root{
  --yellow:#e4c200;
  --yellow-dark:#cfae00;
  --black:#0b0b0b;
  --ink:#1b1b1b;
  --white:#ffffff;
  --grey-text:#bdbdbd;
  --footer:#111111;
  --header:#f4f4f4;
}
*{box-sizing:border-box;margin:0;padding:0}
html,body{width:1200px;height:3261px;overflow:hidden;background:var(--black)}
body{position:relative;font-family:"Open Sans",Arial,sans-serif;color:var(--white)}
.abs{position:absolute}

/* header */
.site-header{left:0;top:0;width:1200px;height:126px;background:var(--header)}
.brand{left:76px;top:36px;width:310px;text-align:center;color:var(--ink)}
.brand-name{font-family:"Cinzel",serif;font-size:33px;letter-spacing:1px;line-height:1}
.brand-tag{font-family:"Cormorant Garamond",serif;font-size:19px;margin-top:8px;color:#333;white-space:nowrap}
.nav{left:430px;top:67px;display:flex;font-family:"Raleway",sans-serif;font-size:13.5px;font-weight:600;color:#333}
.nav a{display:block;padding:0 13px;height:42px;line-height:42px;text-decoration:none;color:inherit}
.nav a.active{background:var(--yellow);color:var(--white);padding:0 16px}
.cta-top{left:965px;top:11px;width:157px;height:48px;background:var(--yellow);color:var(--white);font-family:"Raleway",sans-serif;font-weight:600;font-size:16px;text-align:center;line-height:48px}

/* hero */
.hero{left:0;top:126px;width:1200px;height:548px;background:
  radial-gradient(ellipse 260px 320px at 900px 200px,#8a7a70 0%,rgba(80,70,64,0) 100%),
  linear-gradient(110deg,#6a6a6a 0%,#8a8a8a 30%,#4a4a4a 60%,#1d1d1d 100%)}
.hero-panel{left:109px;top:274px;width:630px;height:232px}
.hero-title{left:238px;top:333px;font-family:"Raleway",sans-serif;font-weight:700;font-size:52px;color:var(--yellow);white-space:nowrap}
.hero-sub{left:246px;top:402px;font-family:"Cormorant Garamond",serif;font-size:21px;color:var(--ink);white-space:nowrap}
.hero-arrow{left:648px;top:458px}
.hero-dots{left:1152px;top:312px;display:flex;flex-direction:column;gap:14px}
.hero-dots span{width:16px;height:16px;border:2px solid var(--yellow);border-radius:50%}
.hero-dots span.on{background:var(--yellow)}
.dark-band{left:0;top:674px;width:1200px;height:840px;background:var(--black)}

/* services */
.service{top:630px;width:333px;height:294px}
.service .photo{width:100%;height:231px}
.service .label{height:63px;background:var(--yellow);color:var(--white);font-family:"Cinzel",serif;font-size:23px;text-align:center;line-height:63px}

/* welcome */
.section-title{width:1200px;left:0;text-align:center;font-family:"Cinzel",serif;font-size:40px;color:var(--yellow)}
.welcome-text{left:150px;top:1054px;width:900px;text-align:center;font-size:12.5px;line-height:27px;color:var(--grey-text)}
.welcome-text p+p{margin-top:12px}

/* consultation */
.consult{left:0;top:1511px;width:1200px;height:380px;background:var(--yellow)}
.video{left:257px;top:1224px;width:687px;height:385px;border:6px solid var(--yellow);background:var(--black)}
.video .frame{position:absolute;left:0;top:0;width:100%;height:336px;background:radial-gradient(ellipse at 50% 45%,#b07a5a 0%,#7a4a36 40%,#3a2722 100%)}
.video .controls{position:absolute;left:0;bottom:0;width:100%;height:37px;background:#151515}
.video .time{position:absolute;left:50px;top:-16px;background:#fff;color:#111;font-size:12px;padding:0 10px;line-height:18px}
.consult-title{top:1666px}
.consult-sub{left:0;top:1720px;width:1200px;text-align:center;font-family:"Raleway",sans-serif;font-size:17px;color:var(--white)}
.field{top:1776px;width:281px;height:50px;background:var(--white);color:#999;font-size:13px;line-height:50px;padding-left:18px}
.submit{left:957px;top:1776px;width:165px;height:50px;border:2px solid var(--white);color:var(--white);font-family:"Raleway",sans-serif;font-weight:700;font-size:17px;text-align:center;line-height:46px}

/* testimonials */
.quote{top:2037px;width:333px;height:159px;background:var(--white);color:#333;font-size:12.5px;line-height:25px;text-align:center;padding:20px 24px}
.quote.featured{height:217px;background:var(--yellow);color:var(--white);font-weight:600}
.tail{width:0;height:0;border-left:26px solid transparent;border-right:26px solid transparent;border-top:26px solid var(--white)}
.client{display:flex;align-items:center;gap:10px;font-size:15px;font-weight:600;color:var(--white)}
.client i{display:block;width:68px;height:68px;border-radius:50%;background:var(--white)}
.slide-arrow{top:2092px}

/* gallery */
.gallery{left:0;top:2420px;width:1200px;height:272px;display:flex}
.gallery .tile{flex:1;height:272px;position:relative}
.gallery .tile.active{border:6px solid var(--yellow)}

/* build cta */
.build{left:0;top:2692px;width:1200px;height:128px;background:var(--yellow)}
.build-title{left:218px;top:2735px;font-family:"Cinzel",serif;font-size:31px;color:var(--ink);white-space:nowrap}
.build-btn{left:700px;top:2729px;width:260px;height:54px;border:2px solid var(--white);color:var(--white);font-family:"Raleway",sans-serif;font-weight:600;font-size:20px;text-align:center;line-height:50px}

/* footer */
.site-footer{left:0;top:2820px;width:1200px;height:376px;background:var(--footer)}
.footer-mark{left:290px;top:2935px;font-family:"Cinzel",serif;font-size:92px;color:#1d1d1d;line-height:1;white-space:nowrap}
.footer-mark small{display:block;font-family:"Cormorant Garamond",serif;font-size:58px;margin-left:-30px}
.footer-head{font-family:"Raleway",sans-serif;font-weight:700;font-size:16px;color:var(--yellow)}
.sitemap{left:80px;top:2894px;font-size:12.5px;line-height:35.5px;color:var(--white)}
.sitemap li{list-style:none}
.sitemap li.current{color:var(--yellow)}
.contact-item{left:339px;display:flex;gap:18px;font-size:12.5px;line-height:25px;color:var(--grey-text)}
.contact-item svg{flex:none;margin-top:3px}
.socials{left:333px;top:3118px;display:flex;gap:12px}
.socials span{width:44px;height:44px;border:3px solid var(--yellow);border-radius:50%}
.team-photo{left:717px;top:2837px;width:392px;height:320px;background:radial-gradient(ellipse 200px 170px at 50% 55%,#5b5b5b 0%,#3a3a3a 55%,rgba(17,17,17,0) 100%)}
.copyright{left:0;top:3196px;width:1200px;height:65px;border-top:1px solid #222;background:var(--footer);text-align:center;font-size:13px;line-height:64px;color:var(--grey-text)}
.copyright b{color:var(--yellow);font-weight:400}
</style>
</head>
<body>

<header class="site-header abs">
  <div class="brand abs">
    <div class="brand-name">Marven Holt</div>
    <div class="brand-tag">Health, Wellness, Fitness, Consultants</div>
  </div>
  <nav class="nav abs">
    <a class="active">HOME</a><a>HEALTH</a><a>WELLNESS</a><a>FITNESS</a><a>OUR TEAM</a><a>TESTIMONIALS</a><a>CONTACT</a>
  </nav>
  <div class="cta-top abs">BRISK FORGE</div>
</header>

<section class="hero abs" role="img" aria-label="Woman training with weights in a gym"></section>
<svg class="hero-panel abs" viewBox="0 0 630 232" width="630" height="232">
  <polygon points="0,0 520,0 630,232 0,232" fill="#ffffff"/>
  <polygon points="0,0 180,0 0,150" fill="#e4c200"/>
  <polygon points="440,0 520,0 630,232 560,232" fill="#e4c200"/>
</svg>
<div class="hero-title abs">Ready To Start ?</div>
<div class="hero-sub abs">Health, Wellness, Fitness, Consultants</div>
<svg class="hero-arrow abs" width="38" height="16" viewBox="0 0 38 16"><path d="M0 8h32M26 2l8 6-8 6" stroke="#111" stroke-width="3" fill="none"/></svg>
<div class="hero-dots abs"><span></span><span></span><span class="on"></span><span></span><span></span></div>

<div class="dark-band abs"></div>

<article class="service abs" style="left:78px">
  <div class="photo" role="img" aria-label="Group stretching outdoors" style="background:linear-gradient(180deg,#cfe0b0 0%,#9fc07a 45%,#6d9a4a 100%)"></div>
  <div class="label">Health</div>
</article>
<article class="service abs" style="left:435px">
  <div class="photo" role="img" aria-label="Woman stretching on a beach at sunset" style="background:linear-gradient(180deg,#f3d3a0 0%,#e9b877 40%,#a07a5a 75%,#6a523f 100%)"></div>
  <div class="label">Wellness</div>
</article>
<article class="service abs" style="left:789px">
  <div class="photo" role="img" aria-label="Group doing kettlebell push-ups" style="background:linear-gradient(180deg,#e8e8e8 0%,#a8a8a8 45%,#4e4e4e 100%)"></div>
  <div class="label">Fitness</div>
</article>

<h1 class="section-title abs" style="top:986px">Welcome To Marven Holt</h1>
<div class="welcome-text abs">
  <p>Marven Holt are leading consultants to the Health, Wellness and Fitness industry, with over 25 years experience working with some of the biggest global worldwide brands from equipment providers and facility operators.</p>
  <p>To mass participation events and obstacle course races. Marven Holt is a multi disciplined business specialising in helping brands grow through insight, strategy creation and valuable sector collaboration, recent clients include the exclusive distribution of Brisk Forge bodyweight training products for the UK and Ireland, exclusive distribution of fitness app Pulse Trackly, Ridgeline Dash Race, Crest Volley</p>
</div>

<section class="consult abs"></section>
<div class="video abs">
  <div class="frame" role="img" aria-label="Video still of a young obstacle race runner"></div>
  <div class="controls">
    <div class="time">46:00</div>
    <svg width="687" height="37" viewBox="0 0 687 37">
      <rect x="14" y="12" width="4" height="13" fill="#fff"/><rect x="22" y="12" width="4" height="13" fill="#fff"/>
      <rect x="46" y="17" width="556" height="3" fill="#555"/><circle cx="52" cy="18.5" r="4" fill="#fff"/>
      <path d="M616 14h5l6-5v19l-6-5h-5z" fill="#fff"/>
      <rect x="648" y="11" width="16" height="15" fill="none" stroke="#fff" stroke-width="2"/>
    </svg>
  </div>
</div>
<h2 class="section-title consult-title abs" style="color:var(--ink)">Need Free Consultation</h2>
<div class="consult-sub abs">Need a free quote, or have a question? Get in touch!</div>
<div class="field abs" style="left:78px">Name *</div>
<div class="field abs" style="left:372px">Email *</div>
<div class="field abs" style="left:665px">Phone *</div>
<div class="submit abs">SUBMIT</div>

<h2 class="section-title abs" style="top:1957px">What Our Client Say</h2>
<svg class="slide-arrow abs" style="left:28px" width="16" height="48" viewBox="0 0 16 48"><path d="M14 2L2 24l12 22" stroke="#666" stroke-width="2" fill="none"/></svg>
<svg class="slide-arrow abs" style="left:1158px" width="16" height="48" viewBox="0 0 16 48"><path d="M2 2l12 22L2 46" stroke="#666" stroke-width="2" fill="none"/></svg>

<div class="quote abs" style="left:78px">"Working alongside the Marven Holt &amp; Vale Leisure team with the Weight Loss Challenge at Larkmoor Hospital has been a really rewarding and learning experience"</div>
<div class="tail abs" style="left:215px;top:2196px"></div>
<div class="quote featured abs" style="left:435px">" Ridgeline Dash Race and Marven Holt first collaborated in 2015. Owen and the Marven Holt team have showed impeccable drive, commitment, passion and integrity throughout our partnership. With the help of the Marven Holt team Ridgeline Dash Race have "</div>
<div class="tail abs" style="left:572px;top:2254px;border-top-color:var(--yellow)"></div>
<div class="quote abs" style="left:789px">" Brayfield Community Leisure commissioned Marven Holt in January 2015 to provide sales training to a new group of Sales Consultants that had been employed"</div>
<div class="tail abs" style="left:926px;top:2196px"></div>

<div class="client abs" style="left:100px;top:2231px"><i></i>Civic Care</div>
<div class="client abs" style="left:449px;top:2292px"><i></i>Ridgeline Dash</div>
<div class="client abs" style="left:812px;top:2231px"><i></i>Brayfield</div>

<section class="gallery abs">
  <div class="tile" role="img" aria-label="Group class on rowing machines" style="background:linear-gradient(135deg,#e0e0e0 0%,#b8a898 45%,#6a5646 100%)"></div>
  <div class="tile active" role="img" aria-label="Obstacle race runners crossing water" style="background:linear-gradient(180deg,#c4c8ca 0%,#9aa3a8 40%,#7d8a6c 75%,#5f6a50 100%)">
    <svg style="position:absolute;left:122px;top:104px" width="64" height="64" viewBox="0 0 64 64"><circle cx="26" cy="26" r="18" fill="none" stroke="#111" stroke-width="5"/><path d="M39 39l18 18" stroke="#111" stroke-width="7" stroke-linecap="round"/><path d="M18 26h16M26 18v16" stroke="#111" stroke-width="4"/></svg>
  </div>
  <div class="tile" role="img" aria-label="Athlete lifting a barbell outdoors" style="background:linear-gradient(180deg,#d2d2d2 0%,#9a968c 45%,#4f4a40 100%)"></div>
  <div class="tile" role="img" aria-label="Man holding a plank on a wet floor" style="background:linear-gradient(180deg,#a6b4bd 0%,#7e8d97 40%,#2e3a44 100%)"></div>
</section>

<section class="build abs"></section>
<div class="build-title abs">Build Your Business Today</div>
<div class="build-btn abs">DROP A MESSGE</div>

<footer class="site-footer abs"></footer>
<div class="footer-mark abs">Marven Holt<small>Health, Wellness, Fitness</small></div>
<div class="team-photo abs" role="img" aria-label="Team of fitness coaches holding exercise equipment"></div>
<div class="footer-head abs" style="left:80px;top:2858px">SITEMAP</div>
<ul class="sitemap abs">
  <li class="current">» Home</li><li>» Health</li><li>» Wellness</li><li>» Fitness</li><li>» Our Team</li><li>» Testimonials</li><li>» Contact Us</li><li>» Brisk Forge</li>
</ul>
<div class="footer-head abs" style="left:339px;top:2858px">CONTACT US</div>
<div class="contact-item abs" style="top:2898px">
  <svg width="22" height="20" viewBox="0 0 22 20"><path d="M1 4l6-3 8 3 6-3v15l-6 3-8-3-6 3z M7 1v15M15 4v15" stroke="#ccc" stroke-width="1.5" fill="none"/></svg>
  <div>The Coachworks , Northfold UK &amp;<br>Ireland</div>
</div>
<div class="contact-item abs" style="top:2960px">
  <svg width="22" height="20" viewBox="0 0 22 20"><path d="M4 1l4 4-2 3c1 3 4 6 7 7l3-2 4 4-3 3C9 19 2 12 1 4z" stroke="#ccc" stroke-width="1.5" fill="none"/></svg>
  <div>07-500-410-912 &nbsp;&nbsp;or<br>01-600-427-315</div>
</div>
<div class="contact-item abs" style="top:3022px">
  <svg width="22" height="20" viewBox="0 0 22 20"><rect x="1" y="3" width="20" height="14" stroke="#ccc" stroke-width="1.5" fill="none"/><path d="M1 3l10 8 10-8" stroke="#ccc" stroke-width="1.5" fill="none"/></svg>
  <div>hello@marvenholt.com</div>
</div>
<div class="contact-item abs" style="top:3062px">
  <svg width="22" height="20" viewBox="0 0 22 22"><circle cx="11" cy="11" r="9" stroke="#ccc" stroke-width="1.5" fill="none"/><ellipse cx="11" cy="11" rx="4" ry="9" stroke="#ccc" stroke-width="1.5" fill="none"/><path d="M2 11h18" stroke="#ccc" stroke-width="1.5"/></svg>
  <div>www.marvenholt.com</div>
</div>
<div class="socials abs"><span aria-label="Social link"></span><span aria-label="Social link"></span></div>
<div class="copyright abs"><b>©Marven Holt</b> - 2017 All Right Reserved.</div>

</body>
</html>
```